Animal Eye Clinic needs a Business card

We are a new veterinary ophthalmology practice (Ridgeline Pet Vision Care) and we need a business card designed. We only see animal eyes - we are not a regular veterinary clinic. We already have a logo. We are looking for a professional, good looking business card to hand out to our clients. We are looking for something simple but professional and contemporary. Our logo is likely the only picture/graphic that needs to be on the card.
Updates

Contact Information for Business Card

Delia Vossman, BSc, DVM, MSc, DipACVO
Veterinary Ophthalmologist

Phone: 250.418.3927
Email: ridgelinepetvisioncare@mailbox-example.net
Website: ridgelinepetvisioncare-example.net
Address: 1874 Thornbury Rd
Kelowna, BC, V1X 4M9

Colors

Designer to choose colors to be used in the design.

Requirements
Must have
• Our logo (attached)

```html
<!DOCTYPE html>
<html lang="en">
<head>
<meta charset="utf-8">
<title>Ridgeline Pet Vision Care – Business Card</title>
<link rel="stylesheet" href="https://fonts.googleapis.com/css2?family=Open+Sans:wght@700;800&family=Roboto:wght@400;500&display=swap">
<style>
  :root {
    --page: #d9d9d9;
    --card: #4b4b4d;
    --teal: #0e8ea2;
    --white: #ffffff;
    --emboss-light: #5d5d60;
    --emboss-dark: #3f3f41;
  }
  * { margin: 0; padding: 0; box-sizing: border-box; }
  html, body { width: 1200px; height: 1125px; overflow: hidden; }
  body {
    background: var(--page);
    font-family: "Roboto", Arial, sans-serif;
    position: relative;
  }
  .card {
    position: absolute;
    left: 150px;
    width: 900px;
    height: 514px;
    background: var(--card);
    border-bottom: 4px solid var(--teal);
    overflow: hidden;
  }
  .card--front { top: 28px; }
  .card--back { top: 583px; }

  /* Front */
  .front-illustration {
    position: absolute;
    left: 40px;
    top: 60px;
    width: 430px;
    height: 430px;
    border-radius: 50%;
    background: linear-gradient(135deg, var(--teal) 0%, var(--teal) 70%, #f2f2f2 71%, #ffffff 100%);
  }
  .front-wordmark {
    position: absolute;
    left: 500px;
    top: 215px;
    color: var(--teal);
    font-family: "Open Sans", Arial, sans-serif;
    font-weight: 800;
    text-transform: uppercase;
    line-height: 1.15;
  }
  .front-wordmark .line-top { display: block; font-size: 26px; letter-spacing: 14px; }
  .front-wordmark .line-main { display: block; font-size: 38px; letter-spacing: 1px; }

  /* Back */
  .back-brand {
    position: absolute;
    left: 60px;
    top: 40px;
    display: flex;
    align-items: center;
    gap: 16px;
  }
  .brand-dot {
    width: 56px; height: 56px;
    border-radius: 50%;
    background: var(--teal);
  }
  .back-wordmark {
    color: var(--teal);
    font-family: "Open Sans", Arial, sans-serif;
    font-weight: 800;
    text-transform: uppercase;
    line-height: 1.1;
  }
  .back-wordmark .line-top { display: block; font-size: 17px; letter-spacing: 10px; }
  .back-wordmark .line-main { display: block; font-size: 28px; }

  .back-illustration {
    position: absolute;
    left: 470px;
    top: 50px;
    width: 470px;
    height: 470px;
    border-radius: 50%;
    background: linear-gradient(160deg, var(--emboss-dark) 0%, var(--emboss-light) 60%, #6a6a6d 100%);
  }

  .contact {
    position: absolute;
    left: 60px;
    top: 140px;
    color: var(--white);
    font-size: 21px;
    line-height: 1.3;
  }
  .person-name {
    display: flex;
    align-items: center;
    gap: 12px;
    color: var(--teal);
    font-family: "Open Sans", Arial, sans-serif;
    font-weight: 800;
    font-size: 26px;
    letter-spacing: 3px;
    text-transform: uppercase;
  }
  .person-name svg { width: 24px; height: 20px; flex: none; }
  .credentials { color: var(--teal); padding-left: 36px; font-size: 20px; }
  .role { padding-left: 36px; margin-bottom: 26px; }
  .address { margin-bottom: 14px; }
  .contact-row { display: flex; align-items: center; gap: 8px; }
  .contact-row svg { width: 18px; height: 18px; flex: none; fill: var(--teal); }
</style>
</head>
<body>

<section class="card card--front" aria-label="Business card front">
  <div class="front-illustration" role="img" aria-label="Logo illustration: horse, dog and cat heads in profile"></div>
  <h1 class="front-wordmark">
    <span class="line-top">Ridgeline</span>
    <span class="line-main">Pet Vision Care</span>
  </h1>
</section>

<section class="card card--back" aria-label="Business card back">
  <div class="back-illustration" role="img" aria-label="Embossed logo illustration: horse, dog and cat heads"></div>

  <div class="back-brand">
    <span class="brand-dot"></span>
    <p class="back-wordmark">
      <span class="line-top">Ridgeline</span>
      <span class="line-main">Pet Vision Care</span>
    </p>
  </div>

  <div class="contact">
    <h2 class="person-name">
      <svg viewBox="0 0 24 20"><polygon points="0,0 24,10 0,20" fill="#0e8ea2"/></svg>
      Delia Vossman
    </h2>
    <p class="credentials">BSc, DVM, MSc, DipACVO</p>
    <p class="role">Veterinary Ophthalmologist</p>
    <p class="address">1874 Thornbury Rd<br>Kelowna, BC, V1X 4M9</p>
    <p class="contact-row">
      <svg viewBox="0 0 24 24"><path d="M6.6 10.8a15.1 15.1 0 0 0 6.6 6.6l2.2-2.2c.3-.3.7-.4 1-.2 1.1.4 2.3.6 3.6.6.6 0 1 .4 1 1V20c0 .6-.4 1-1 1A17 17 0 0 1 3 4c0-.6.4-1 1-1h3.5c.6 0 1 .4 1 1 0 1.3.2 2.5.6 3.6.1.3 0 .7-.2 1z"/></svg>
      250.418.3927
    </p>
    <p class="contact-row">
      <svg viewBox="0 0 24 24"><path d="M2 5h20v14H2z M2 5l10 8 10-8" fill="none" stroke="#0e8ea2" stroke-width="2"/></svg>
      ridgelinepetvisioncare@mailbox-example.net
    </p>
    <p class="contact-row">
      <svg viewBox="0 0 24 24"><circle cx="12" cy="12" r="10" fill="none" stroke="#0e8ea2" stroke-width="2"/><path d="M2 12h20M12 2c3 3 3 17 0 20M12 2c-3 3-3 17 0 20" fill="none" stroke="#0e8ea2" stroke-width="1.6"/></svg>
      ridgelinepetvisioncare-example.net
    </p>
  </div>
</section>

</body>
</html>
```